Corvane Card

The logo is the Spanish flag colors I want a vibrant eye catching design with the yellow / red colors over either Navy or white background or black even ,
Would like a 2D feel to the logo with another lighter color logo under it look ,

Contact Information for Business Card

Corvane Flooring
Teodor Vashkin
Main Number
Cell Number
Fax Number

Website on the side of the card somewhere

Font styles to use
Sans Serif

Colors
ec1f27
ffc214

Requirements
Must have
• 2 logos feel one is bolder and the other one underneath very light

```html
<!DOCTYPE html>
<html lang="en">
<head>
<meta charset="utf-8">
<title>Corvane Card</title>
<link rel="stylesheet" href="https://fonts.googleapis.com/css2?family=Montserrat:wght@700;800&family=Arimo:wght@400&display=swap">
<style>
  :root {
    --red: #ec1f27;
    --yellow: #ffc214;
    --ink: #222222;
    --stage: #2a2a2a;
    --white: #ffffff;
    --rule: #4a4a4a;
  }
  * { box-sizing: border-box; margin: 0; padding: 0; }
  html, body { width: 1200px; height: 1015px; overflow: hidden; }
  body {
    background: radial-gradient(ellipse at 50% 45%, #3a3a3a 0%, var(--stage) 55%, #141414 100%);
    font-family: "Arimo", Arial, sans-serif;
    position: relative;
  }
  .card {
    position: absolute;
    left: 250px;
    width: 700px;
    height: 400px;
    overflow: hidden;
    box-shadow: 0 18px 40px rgba(0,0,0,.55);
  }
  .card--front { top: 80px; background: var(--red); }
  .card--back  { top: 535px; background: var(--ink); }

  /* brand lockup */
  .brand {
    position: absolute;
    display: flex;
    align-items: center;
    gap: 18px;
  }
  .brand__square { width: 64px; height: 64px; flex: none; }
  .brand__name {
    font-family: "Montserrat", sans-serif;
    font-weight: 800;
    font-size: 40px;
    line-height: 1.05;
    letter-spacing: 1px;
    text-transform: uppercase;
  }

  .card--front .brand { left: 0; right: 0; top: 95px; justify-content: center; }
  .card--front .brand__square { background: var(--yellow); }
  .card--front .brand__name { color: var(--white); }

  .front__band {
    position: absolute; left: 0; right: 0; bottom: 22px; height: 62px;
    background: var(--yellow);
    display: flex; align-items: center; justify-content: center;
  }
  .front__website {
    color: var(--white);
    font-size: 19px;
    letter-spacing: 3px;
  }

  .card--back .brand { left: 55px; top: 150px; }
  .card--back .brand__square { background: var(--yellow); }
  .card--back .brand__name { color: var(--red); font-size: 34px; }

  .back__divider {
    position: absolute; left: 375px; top: 70px; width: 1px; height: 200px;
    background: var(--rule);
  }
  .contact { position: absolute; left: 410px; top: 78px; }
  .contact__name {
    font-family: "Montserrat", sans-serif;
    font-weight: 800;
    font-size: 26px;
    text-transform: uppercase;
    margin-bottom: 22px;
    letter-spacing: .5px;
  }
  .contact__first { color: var(--red); }
  .contact__last  { color: var(--yellow); }
  .contact__list { list-style: none; }
  .contact__item {
    display: flex; align-items: center; gap: 12px;
    color: var(--white); font-size: 18px; line-height: 1; margin-bottom: 13px;
  }
  .contact__icon { width: 18px; height: 18px; flex: none; }

  .back__stripe { position: absolute; left: 0; right: 0; bottom: 0; height: 14px; display: flex; }
  .back__stripe-red { flex: 0 0 62%; background: var(--red); }
  .back__stripe-yellow { flex: 1; background: var(--yellow); }
</style>
</head>
<body>

<section class="card card--front" aria-label="Card front">
  <div class="brand">
    <span class="brand__square"></span>
    <span class="brand__name">Corvane<br>Flooring</span>
  </div>
  <div class="front__band">
    <span class="front__website">www.corvaneflooring.com</span>
  </div>
</section>

<section class="card card--back" aria-label="Card back">
  <div class="brand">
    <span class="brand__square"></span>
    <span class="brand__name">Corvane<br>Flooring</span>
  </div>

  <div class="back__divider"></div>

  <div class="contact">
    <p class="contact__name"><span class="contact__first">Teodor</span> <span class="contact__last">Vashkin</span></p>
    <ul class="contact__list">
      <li class="contact__item">
        <svg class="contact__icon" viewBox="0 0 24 24" aria-hidden="true"><path fill="#ec1f27" d="M2 9c0-3 4-5 10-5s10 2 10 5v2h-5V9c-1-1-3-1.5-5-1.5S8 8 7 9v2H2zM6 12h12l2 8H4z"/></svg>
        <span>202 555 0147</span>
      </li>
      <li class="contact__item">
        <svg class="contact__icon" viewBox="0 0 24 24" aria-hidden="true"><rect x="5" y="2" width="14" height="20" rx="2" fill="none" stroke="#ec1f27" stroke-width="2.5"/></svg>
        <span>202 555 0183</span>
      </li>
      <li class="contact__item">
        <svg class="contact__icon" viewBox="0 0 24 24" aria-hidden="true"><rect x="6" y="2" width="12" height="6" fill="#ec1f27"/><rect x="2" y="9" width="20" height="9" rx="2" fill="#ec1f27"/><rect x="6" y="15" width="12" height="7" fill="#ec1f27" stroke="#222" stroke-width="1.5"/></svg>
        <span>202 555 0129</span>
      </li>
      <li class="contact__item">
        <svg class="contact__icon" viewBox="0 0 24 24" aria-hidden="true"><rect x="2" y="5" width="20" height="14" fill="#ec1f27"/><path d="M2 5l10 8 10-8" fill="none" stroke="#222" stroke-width="1.8"/></svg>
        <span>hello@corvaneflooring.com</span>
      </li>
    </ul>
  </div>

  <div class="back__stripe">
    <span class="back__stripe-red"></span>
    <span class="back__stripe-yellow"></span>
  </div>
</section>

</body>
</html>
```